Fitness Equipment Repair Business Needs a Catchy New Business Card

We have an existing business card, however, it is quite plain and boring. We are expanding primarily in the commercial area (gyms, studios, apartment complexes etc). The business card will serve as eye candy to those managers/owners that can't be met for a face to face.
Originally I was planning for a brochure as well, but all of our information is better summarized on our website. (brightloopservice.ca).
I would like the card to match the colour scheme of the website and utilize the logo. It should have a professional clean feel to it, however, a little colouring outside the lines wouldn't hurt.
The example card is for my service technician (Colin Marsh). If possible I would like to be able to edit the text to use for more than one person.

Industry/Entity Type

Appliance Repair

Contact Information for Business Card

Clean, crisp and professional but needs to be eye catching. Preferably using the black, white and red colour scheme matching the website. Double sided would be nice, but is not necessary.

Colors
ec1f27
ffffff
000000

Requirements
Must have
• Must be able to edit name, phone number and title to use for multiple people. Must show the company website (brightloopservice.ca).

```html
<!DOCTYPE html>
<html lang="en">
<head>
<meta charset="utf-8">
<title>Bright Loop Service – Business Card</title>
<link rel="stylesheet" href="https://fonts.googleapis.com/css2?family=Arimo:wght@700&family=Arvo:ital,wght@0,400;0,700;1,400&display=swap">
<style>
  :root {
    --red: #ec1f27;
    --white: #ffffff;
    --black: #000000;
    --backdrop: #3b3531;
    --figure-tone-a: #2a2a2a;
    --figure-tone-b: #0c0c0c;
    --rule: #8a8a8a;
  }
  * { box-sizing: border-box; margin: 0; padding: 0; }
  html, body { width: 1200px; height: 780px; overflow: hidden; }
  body { background: var(--backdrop); font-family: "Arvo", serif; color: var(--white); position: relative; }

  .card {
    position: absolute;
    width: 540px;
    height: 310px;
    background: var(--black);
    box-shadow: 0 14px 30px rgba(0,0,0,.45);
    overflow: hidden;
  }
  .card--front { left: 50px; top: 90px; }
  .card--back  { left: 610px; top: 380px; }

  /* front */
  .front-figure {
    position: absolute; left: 0; top: 20px; width: 210px; height: 270px;
    background: radial-gradient(ellipse at 55% 45%, var(--figure-tone-a), var(--figure-tone-b) 75%);
    border-radius: 8px;
  }
  .company-name {
    position: absolute; left: 240px; top: 70px; width: 280px; text-align: right;
    font-family: "Arimo", sans-serif; font-weight: 700; font-variant: small-caps;
    font-size: 25px; letter-spacing: 1.5px;
  }
  .tagline {
    position: absolute; left: 250px; top: 118px; width: 270px; text-align: right;
    font-style: italic; font-size: 13px; line-height: 1.5;
  }
  .front-web {
    position: absolute; left: 250px; top: 250px; width: 270px; text-align: right;
    font-size: 14px;
  }

  /* back */
  .back-figure {
    position: absolute; left: 60px; top: 36px; width: 170px; height: 200px;
    background: radial-gradient(ellipse at 50% 45%, var(--figure-tone-a), var(--figure-tone-b) 75%);
    border-radius: 8px;
  }
  .brand-name {
    position: absolute; left: 35px; top: 248px; width: 220px; text-align: center;
    font-family: "Arvo", serif; font-weight: 400; font-size: 15px;
    color: var(--white);
  }
  .divider {
    position: absolute; left: 285px; top: 40px; width: 1px; height: 230px;
    background: var(--rule);
  }
  .contact { position: absolute; left: 305px; top: 50px; width: 220px; }
  .contact-name { font-weight: 700; font-size: 21px; line-height: 1.05; }
  .contact-title { color: var(--red); font-size: 14px; margin-bottom: 12px; }
  .contact-address { font-size: 14px; line-height: 1.35; margin-bottom: 10px; }
  .contact-line { display: flex; align-items: center; gap: 8px; font-size: 14px; line-height: 1.55; }
  .contact-line svg { width: 13px; height: 13px; flex: none; fill: var(--red); }
  .contact-web { font-size: 14px; margin-top: 8px; }
  .contact-web .domain { color: var(--red); }
</style>
</head>
<body>

<section class="card card--front">
  <div class="front-figure" role="img" aria-label="Line illustration of a muscular technician in a hard hat holding a wrench"></div>
  <h1 class="company-name">Bright Loop Service</h1>
  <p class="tagline">when your equipment can't finish the workout, give us a call !</p>
  <p class="front-web">www.brightloopservice.ca</p>
</section>

<section class="card card--back">
  <div class="back-figure" role="img" aria-label="Line illustration of a muscular technician in a hard hat holding a wrench"></div>
  <p class="brand-name">Bright Loop Service</p>
  <div class="divider"></div>
  <div class="contact">
    <p class="contact-name">Colin Marsh</p>
    <p class="contact-title">service technician</p>
    <p class="contact-address">1875 Corran Way NW<br>Edmonton AB T5K 2P4</p>
    <p class="contact-line">
      <svg viewBox="0 0 16 16" aria-hidden="true"><path d="M4 0h8a1 1 0 0 1 1 1v14a1 1 0 0 1-1 1H4a1 1 0 0 1-1-1V1a1 1 0 0 1 1-1zm1 2v10h6V2H5zm3 11a1 1 0 1 0 0 2 1 1 0 0 0 0-2z"/></svg>
      555-310-2846
    </p>
    <p class="contact-line">
      <svg viewBox="0 0 16 16" aria-hidden="true"><path d="M1 5c0-2 3-3 7-3s7 1 7 3v1h-4V5H5v1H1V5zm2 2h10l1 7H2l1-7zm5 1.5a2.5 2.5 0 1 0 0 5 2.5 2.5 0 0 0 0-5z"/></svg>
      555-640-1193
    </p>
    <p class="contact-line">
      <svg viewBox="0 0 16 16" aria-hidden="true"><path d="M0 3h16v10H0V3zm1.5 1.2L8 9l6.5-4.8V4h-13v.2z"/></svg>
      brightloop@mailbox.com
    </p>
    <p class="contact-web">www.<span class="domain">brightloopservice</span>.ca</p>
  </div>
</section>

</body>
</html>
```